Quiet Harbor Prints gallery website

I need a Website for a gallery with a shopify integration or maybe even better also compatible with squarespace.
the website should have following riders: Künstler, Veranstaltungen, Shop, About Us.
some nice examples for inspiration of the website architecture are:
https://www.lindwerkraum.com/
https://www.plattenbau-salon.com/de/
https://moorlichtraum.de/
It should be easy for us to make adaptations and fill the website with new content.
Attached there is the CI an logo for the brand.
Target Market(s)
Art Collectors,
Industry/Entity Type
artgallery
Coding
Coded - Design and coding required
Number of Pages Required
3 page
Font styles to use
Look and feel

```html
<!DOCTYPE html>
<html lang="en">
<head>
<meta charset="utf-8">
<title>Quiet Harbor Prints – Gallery Website</title>
<link href="https://fonts.googleapis.com/css2?family=Open+Sans:wght@300;400;600;700&display=swap" rel="stylesheet">
<style>
:root{
  --ink:#141414;
  --paper:#ffffff;
  --canvas:#ffffff;
  --muted:#555555;
  --line:#d8d8d8;
  --dark:#151515;
  --plum:#3a1838;
  --wood-1:#3b2a1e;
  --wood-2:#8a6a4a;
}
*{box-sizing:border-box;margin:0;padding:0}
html,body{width:1200px;height:3120px;overflow:hidden;background:var(--canvas)}
body{font-family:"Open Sans",sans-serif;color:var(--ink);position:relative}
.view-label{position:absolute;top:28px;font-size:16px;letter-spacing:3px;font-weight:400;color:#333}
.view-label.desk{left:420px}
.view-label.mob{left:925px}

/* shared */
.brand{font-weight:400;color:var(--ink);white-space:nowrap}
.btn{display:inline-block;background:var(--ink);color:#fff;font-weight:700;text-transform:uppercase;text-align:center;letter-spacing:2px;white-space:nowrap}
.ph{display:block}

/* ---------- DESKTOP ---------- */
.desktop{position:absolute;left:113px;top:62px;width:750px;background:var(--paper);box-shadow:0 0 6px rgba(0,0,0,.08)}
.d-header{height:63px;display:flex;align-items:center;justify-content:space-between;padding:0 53px}
.d-header .brand{font-size:10px}
.d-nav{display:flex;align-items:center;gap:22px;font-size:8.5px;letter-spacing:.6px;text-transform:uppercase;color:#333}
.d-nav svg{width:10px;height:10px;stroke:#333;fill:none;stroke-width:1.4}
.d-nav .icons{display:flex;gap:14px}

.d-hero{position:relative;height:346px;background:linear-gradient(180deg,#cfc7bc 0%,#a68c6e 48%,var(--wood-2) 62%,var(--wood-1) 100%);color:#fff}
.d-hero .txt{position:absolute;left:53px;top:150px}
.d-hero .kicker{font-size:11px;letter-spacing:.4px}
.d-hero h1{font-weight:400;font-size:25px;line-height:33px;letter-spacing:.6px;margin-top:4px}
.d-hero .explore{display:inline-block;margin-top:14px;border:1px solid #fff;font-size:8px;letter-spacing:2px;padding:8px 0;width:107px;text-align:center;font-weight:600}
.dots{position:absolute;left:0;right:0;bottom:28px;display:flex;justify-content:center;gap:10px}
.dots i{display:block;width:30px;height:2px;background:rgba(255,255,255,.45)}
.dots i:first-child{background:#fff}

.d-intro{height:584px;text-align:center;padding-top:30px}
.d-intro h2{font-weight:400;font-size:19.5px;line-height:26px;letter-spacing:.2px;width:500px;margin:0 auto}
.d-intro p{font-size:8.6px;line-height:18px;color:#333;width:500px;margin:10px auto 0}
.d-intro h3{font-weight:400;font-size:16px;margin-top:14px}
.event{position:relative;width:552px;margin:10px auto 0;color:#fff;display:flex;flex-direction:column;align-items:center;justify-content:center}
.event.one{height:171px;background:linear-gradient(90deg,#b9ab9a,#a39480 50%,#8a8173)}
.event.two{height:156px;margin-top:15px;background:linear-gradient(90deg,#9a9890,#7e7b74 55%,#5d5a55)}
.event .date{background:#161616;font-size:8px;padding:3px 8px;font-weight:600}
.event .ttl{font-size:16.5px;line-height:23px;margin-top:4px;font-weight:300}
.d-intro .btn{font-size:8px;padding:9px 14px;margin-top:12px}

.d-art{height:608px;background:radial-gradient(ellipse 60% 50% at 100% 0%,#3a1838 0%,rgba(58,24,56,.4) 50%,rgba(21,21,21,0) 100%),var(--dark);color:#fff;padding:36px 53px 0}
.d-art .top{display:flex;justify-content:space-between}
.d-art .kicker{font-size:6.5px;font-weight:700}
.d-art h2{font-weight:400;font-size:21px;line-height:26px;margin-top:6px}
.d-art .top p{width:345px;font-size:8.4px;line-height:16.5px;font-weight:600;margin-top:10px}
.grid3{display:grid;grid-template-columns:repeat(3,199px);column-gap:23px;margin-top:14px}
.grid3.r2{margin-top:26px}
.art-card{text-align:center}
.art-card .ph{height:146px}
.art-card .cat{font-size:7px;font-weight:700;letter-spacing:1px;margin-top:11px}
.art-card .nm{font-size:11.5px;margin-top:4px;letter-spacing:.3px}
.d-art .viewall{display:block;width:48px;margin:30px auto 0;font-size:8px;font-weight:600;letter-spacing:1.5px;padding-bottom:3px;border-bottom:1px solid #fff;text-align:center;white-space:nowrap}

.d-popular{height:397px;text-align:center;padding-top:34px}
.d-popular h2{font-weight:400;font-size:20px}
.d-popular p{font-size:8.6px;line-height:15px;width:420px;margin:6px auto 0;color:#333}
.frames{display:flex;gap:34px;justify-content:center;margin-top:20px}
.frame .ph{width:135px;height:183px;border:4px solid #111}
.frame .nm{font-size:11px;margin-top:10px;letter-spacing:.4px}
.d-popular .btn{font-size:8px;padding:9px 0;width:97px;margin-top:18px}

.d-news{height:170px;background:linear-gradient(90deg,#121212 0%,#1c1a18 45%,#3b1c3a 100%);color:#fff;display:flex;align-items:center;padding-left:123px}
.d-news .kicker{font-size:6.5px;font-weight:700}
.d-news h2{font-weight:400;font-size:20px;margin-top:4px}
.d-news small{display:block;font-size:6.5px;font-weight:600;margin-top:3px}
.input{display:flex;align-items:center;justify-content:space-between;background:#fff;color:#555}
.d-news .input{width:297px;height:27px;margin-left:14px;padding:0 8px;font-size:7.5px}
.input svg{stroke:#333;fill:none;stroke-width:1.3}

.d-projects{height:592px;text-align:center;padding-top:40px}
.d-projects h2{font-weight:400;font-size:20px}
.d-projects p{font-size:8.6px;margin-top:3px;color:#333}
.proj-big{position:relative;width:552px;height:221px;margin:16px auto 0;background:linear-gradient(90deg,#7a5d3a 0%,#c9b8a0 35%,#d8ccbb 62%,#1f2530 78%,#2c3440 100%)}
.proj-big span{position:absolute;left:17px;bottom:10px;color:#fff;font-size:15px;font-weight:300}
.proj-row{display:flex;justify-content:center;gap:16px;margin-top:18px}
.proj-row .ph{width:268px;height:170px}
.d-projects .btn{font-size:8px;padding:9px 0;width:97px;margin-top:27px}

.d-footer{height:236px;background:var(--dark);color:#fff;padding:38px 53px 0;position:relative}
.f-cols{display:flex}
.f-logo{width:211px;display:flex;flex-direction:column;align-items:center;padding-top:30px}
.f-logo .brand{color:#fff;font-size:15px;font-weight:300}
.social{display:flex;gap:18px;margin-top:22px}
.social i{display:block;width:9px;height:9px;border-radius:50%;background:#fff}
.f-col h4{font-weight:400;font-size:10px;letter-spacing:.6px;margin-bottom:12px}
.f-col li{list-style:none;font-size:8.5px;line-height:22px;color:#ddd}
.f-col.contact{width:212px}
.f-col.quick{width:143px}
.contact li{display:flex;gap:8px;line-height:16px;margin-bottom:6px}
.contact svg{width:9px;height:9px;flex:none;margin-top:3px;stroke:#fff;fill:none;stroke-width:1.5}
.f-bottom{position:absolute;left:53px;right:53px;bottom:20px;border-top:1px solid #333;padding-top:14px;display:flex;justify-content:space-between;align-items:center;font-size:7.5px;color:#aaa}
.f-bottom b{color:#fff;font-weight:400}
.cards{display:flex;gap:10px}
.cards i{display:block;width:22px;height:14px;background:#e8e8e8;border-radius:2px}

/* ---------- MOBILE ---------- */
.mobile{position:absolute;left:896px;top:62px;width:192px;background:var(--paper);box-shadow:0 0 6px rgba(0,0,0,.08)}
.m-pad{padding:0 10px}
.m-header{height:31px;display:flex;align-items:center;justify-content:space-between;padding:0 10px}
.m-header .brand{font-size:5px}
.m-header svg{width:9px;height:8px;stroke:#444;stroke-width:1}
.m-hero{position:relative;height:183px;background:linear-gradient(180deg,#cdc5ba 0%,#a68c6e 50%,var(--wood-2) 66%,var(--wood-1) 100%);color:#fff;padding:58px 0 0 10px}
.m-hero .kicker{font-size:6.5px}
.m-hero h1{font-weight:400;font-size:13.5px;line-height:19px;letter-spacing:.4px;width:140px}
.m-hero .explore{display:inline-block;margin-top:8px;border:1px solid #fff;font-size:5px;letter-spacing:1px;padding:5px 0;width:67px;text-align:center;font-weight:600}
.m-hero .dots{bottom:10px;gap:6px}
.m-hero .dots i{width:18px;height:1.5px}
.m-intro{height:472px;text-align:center;padding-top:15px}
.m-intro h2{font-weight:400;font-size:11.5px;line-height:19px}
.m-intro p{font-size:5.5px;line-height:11px;color:#333;margin-top:6px}
.m-intro h3{font-weight:400;font-size:10.5px;margin-top:12px}
.m-event{height:127px;margin-top:6px;color:#fff;display:flex;flex-direction:column;align-items:center;justify-content:center}
.m-event.one{background:linear-gradient(90deg,#b9ab9a,#8e8474)}
.m-event.two{height:117px;margin-top:10px;background:linear-gradient(90deg,#9a9890,#5d5a55)}
.m-event .date{background:#161616;font-size:5px;padding:2px 5px;font-weight:600}
.m-event .ttl{font-size:11px;line-height:15px;margin-top:3px;font-weight:300}
.m-intro .btn{font-size:5.5px;padding:6px 0;width:84px;margin-top:9px;letter-spacing:1px}
.m-art{height:710px;background:radial-gradient(ellipse 90% 25% at 100% 0%,#3a1838 0%,rgba(58,24,56,.4) 55%,rgba(21,21,21,0) 100%),var(--dark);color:#fff;padding:38px 10px 0}
.m-art .kicker{font-size:4.5px;font-weight:700}
.m-art h2{font-weight:400;font-size:11.5px;line-height:19px;margin-top:3px}
.m-art p{font-size:5.5px;line-height:12px;font-weight:600;margin-top:3px}
.m-card{text-align:center;margin-top:14px}
.m-card .ph{height:125px}
.m-card .cat{font-size:4.5px;font-weight:700;letter-spacing:.8px;margin-top:11px}
.m-card .nm{font-size:8px;margin-top:2px}
.m-art .viewall{display:block;width:32px;margin:14px auto 0;font-size:5px;font-weight:600;letter-spacing:1px;border-bottom:1px solid #fff;padding-bottom:2px;text-align:center;white-space:nowrap}
.m-popular{height:330px;text-align:center;padding-top:22px}
.m-popular h2{font-weight:400;font-size:12px}
.m-popular p{font-size:5.5px;line-height:10.5px;color:#333;margin-top:4px}
.m-popular .frame .ph{width:143px;height:194px;margin:8px auto 0;border:4px solid #111}
.m-popular .nm{font-size:7px;margin-top:6px}
.m-popular .pager{display:flex;gap:4px;justify-content:center;margin-top:14px;align-items:center}
.m-popular .pager i{display:block;width:2px;height:2px;border-radius:50%;background:#999}
.m-popular .pager i:first-child{width:20px;height:2px;border-radius:0;background:#333}
.m-news{height:132px;background:linear-gradient(90deg,#141414 0%,#1c1a18 50%,#3b1c3a 100%);color:#fff;padding:33px 10px 0}
.m-news .kicker{font-size:4.5px;font-weight:700}
.m-news h2{font-weight:400;font-size:11.5px;margin-top:1px}
.m-news small{display:block;font-size:4.5px;font-weight:600}
.m-news .input{height:19px;margin-top:10px;padding:0 5px;font-size:5px}
.m-projects{height:607px;text-align:center;padding-top:20px}
.m-projects h2{font-weight:400;font-size:12px}
.m-projects p{font-size:5.5px;margin-top:1px;color:#333}
.m-proj{position:relative;height:158px;margin-top:16px}
.m-proj.first{margin-top:6px}
.m-proj span{position:absolute;left:6px;bottom:8px;color:#fff;font-size:10px;font-weight:300}
.m-projects .btn{font-size:5.5px;padding:6px 0;width:68px;margin-top:12px;letter-spacing:1px}
.m-footer{height:531px;background:var(--dark);color:#fff;padding:30px 10px 0}
.m-footer .brand{color:#fff;font-size:9px;font-weight:300}
.m-footer h4{font-weight:400;font-size:6.5px;letter-spacing:.4px;margin-bottom:6px}
.m-footer .block{border-bottom:1px solid #333;padding:18px 0 14px}
.m-footer .block.first{padding-top:0;border-bottom:none}
.m-footer li{list-style:none;font-size:5px;line-height:15px;color:#ddd}
.m-footer .contact li{line-height:10px;margin-bottom:4px;gap:5px}
.m-footer .contact svg{width:6px;height:6px;margin-top:2px}
.m-footer .social{gap:12px;margin-top:16px}
.m-footer .social i{width:6px;height:6px}
.m-footer .legal{font-size:4.5px;color:#aaa;margin-top:30px;line-height:9px}
.m-footer .cards{gap:5px;margin-top:4px}
.m-footer .cards i{width:14px;height:9px}
</style>
</head>
<body>

<div class="view-label desk">DESKTOP VIEW</div>
<div class="view-label mob">MOBILE VIEW</div>

<main class="desktop">
  <header class="d-header">
    <div class="brand">QUIET HARBOR PRINTS</div>
    <nav class="d-nav">
      <span>Artists</span><span>Events</span><span>Shop</span><span>About Us</span>
      <span class="icons">
        <svg viewBox="0 0 10 10"><circle cx="4.2" cy="4.2" r="3.2"/><path d="M6.6 6.6L9.4 9.4"/></svg>
        <svg viewBox="0 0 10 10"><path d="M5 8.8L1.3 5A2.2 2.2 0 0 1 5 2.2 2.2 2.2 0 0 1 8.7 5z"/></svg>
        <svg viewBox="0 0 10 10"><path d="M.5 1h1.6l1.2 5.4h5L9.4 3H2.7"/><circle cx="4" cy="8.5" r=".7"/><circle cx="7.6" cy="8.5" r=".7"/></svg>
      </span>
    </nav>
  </header>

  <section class="d-hero" role="img" aria-label="Gallery interior with framed paintings on white walls, a wooden floor and a sculpture in the foreground">
    <div class="txt">
      <div class="kicker">BEGIN AN EXPLORATION THROUGH</div>
      <h1>A GALLERY SHOWCASING<br>ARTIST CREATIVIY</h1>
      <span class="explore">EXPLORE</span>
    </div>
    <div class="dots"><i></i><i></i><i></i></div>
  </section>

  <section class="d-intro">
    <h2>THE GALLERY FOR URBAN ART AND CONTEMPORARY ART IN HAMBURG!</h2>
    <p>Lorem ipsum dolor sit amet, consectetur adipiscing elit, sed do eiusmod tempor incididunt ut labore et dolore magna aliqua. Quis ipsum suspendisse ultrices gravida. Risus commodo viverra maecenas accumsan lacus vel facilisis.</p>
    <h3>UPCOMING EVENTS</h3>
    <div class="event one" role="img" aria-label="Collage of a woman in profile surrounded by sunflowers and leaves">
      <span class="date">MAR. 18,2024</span>
      <span class="ttl">Proin scelerisque dolor vitae<br>augue condimentum</span>
    </div>
    <div class="event two" role="img" aria-label="Abstract collage with a large eye and geometric shapes">
      <span class="date">APR. 18,2024</span>
      <span class="ttl">Proin scelerisque dolor vitae<br>augue condimentum</span>
    </div>
    <span class="btn">VIEW ALL EVENTS</span>
  </section>

  <section class="d-art">
    <div class="top">
      <div>
        <div class="kicker">NEW ARTWORK</div>
        <h2>UNVEILING OUR<br>EXCLUSIVE ARTWORK</h2>
      </div>
      <p>Class aptent taciti sociosqu ad litora torquent per conubia nostra, per inceptos himenaeos. Vestibulum non congue ligula, ut sollicitudin arcut taciti sociosqu ad litora torquent per conubia nostra, per inceptos himenaeos.</p>
    </div>
    <div class="grid3">
      <div class="art-card"><span class="ph" role="img" aria-label="Abstract landscape with a glowing sun and orange spheres over teal waves" style="background:linear-gradient(160deg,#2e6d6a 0%,#c8a55a 40%,#d06a2a 70%,#1c3b3c 100%)"></span><div class="cat">CREATIVE</div><div class="nm">MODERN ART</div></div>
      <div class="art-card"><span class="ph" role="img" aria-label="Cubist painting of abstract figures in muted earth tones" style="background:linear-gradient(135deg,#6a5040,#8a6a50 45%,#4a3a30)"></span><div class="cat">CREATIVE</div><div class="nm">MODERN ART</div></div>
      <div class="art-card"><span class="ph" role="img" aria-label="White flower on a soft pink background" style="background:linear-gradient(135deg,#f2ddd2,#e9c8bb)"></span><div class="cat">CREATIVE</div><div class="nm">MODERN ART</div></div>
    </div>
    <div class="grid3 r2">
      <div class="art-card"><span class="ph" role="img" aria-label="Double exposure artwork of a figure blended with hills" style="background:linear-gradient(180deg,#d9d6cf,#9a9a88 55%,#5b5d44)"></span><div class="cat">CREATIVE</div><div class="nm">MODERN ART</div></div>
      <div class="art-card"><span class="ph" role="img" aria-label="Ink splash tree in red and blue over a lake" style="background:linear-gradient(180deg,#eee9e2,#d67a5a 45%,#7a8ea8 75%,#e8e4dc)"></span><div class="cat">CREATIVE</div><div class="nm">MODERN ART</div></div>
      <div class="art-card"><span class="ph" role="img" aria-label="Lone tree with birds above a gold and black landscape" style="background:linear-gradient(180deg,#e8e8e6,#c9c7c0 55%,#8a7a3a 75%,#2a2a2a)"></span><div class="cat">CREATIVE</div><div class="nm">MODERN ART</div></div>
    </div>
    <span class="viewall">VIEW ALL</span>
  </section>

  <section class="d-popular">
    <h2>Our Popular Art</h2>
    <p>Etiam ut libero pulvinar, imperdiet enim vel, euismod dui. Nunc nec feugiat ex. Praesent at eros lectus. Duis iaculis posuere arcu quis pretium.</p>
    <div class="frames">
      <div class="frame"><span class="ph" role="img" aria-label="Framed print of mountains inside a silhouette on a yellow background" style="background:linear-gradient(160deg,#d8b840,#e2e0d8 45%,#222 80%)"></span><div class="nm">CREATIVE ART</div></div>
      <div class="frame"><span class="ph" role="img" aria-label="Framed print of a tree growing from a head in teal and coral" style="background:linear-gradient(180deg,#3a6d72,#d04a3a 50%,#5ab0a8)"></span><div class="nm">CREATIVE ART</div></div>
      <div class="frame"><span class="ph" role="img" aria-label="Framed print of a moonlit abstract figure in navy and cream" style="background:linear-gradient(160deg,#1e2a3a,#d7d2c4 55%,#c46a2a)"></span><div class="nm">CREATIVE ART</div></div>
      <div class="frame"><span class="ph" role="img" aria-label="Framed print of a floral figure in pink and orange on pale blue" style="background:linear-gradient(160deg,#cfe2e4,#e38a9a 45%,#f0a040 75%,#cfe2e4)"></span><div class="nm">CREATIVE ART</div></div>
    </div>
    <span class="btn">VIEW ALL</span>
  </section>

  <section class="d-news">
    <div>
      <div class="kicker">SUBSCRIBE TO</div>
      <h2>OUR NEWSLETTER</h2>
      <small>With our newsletter you won't miss any exhibitions.</small>
    </div>
    <div class="input"><span>Email Address</span><svg width="12" height="8" viewBox="0 0 12 8"><path d="M0 4h11M8 1l3 3-3 3"/></svg></div>
  </section>

  <section class="d-projects">
    <h2>OUR LATEST PROJECTS</h2>
    <p>Quisque lacinia elit nulla, non congue dui dignissim at</p>
    <div class="proj-big" role="img" aria-label="Exhibition hall with colourful abstract paintings on white walls"><span>Hall of Frame</span></div>
    <div class="proj-row">
      <span class="ph" role="img" aria-label="Long gallery corridor lined with vivid paintings" style="background:linear-gradient(90deg,#5a3a2a,#c9b8a0 40%,#8a6a50 70%,#3a2a22)"></span>
      <span class="ph" role="img" aria-label="Dim exhibition room with red paintings and a central display" style="background:linear-gradient(90deg,#3a3430,#7a6a5c 45%,#5a4a40 75%,#2a2420)"></span>
    </div>
    <span class="btn">VIEW ALL</span>
  </section>

  <footer class="d-footer">
    <div class="f-cols">
      <div class="f-logo">
        <div class="brand">QUIET HARBOR PRINTS</div>
        <div class="social"><i></i><i></i><i></i><i></i></div>
      </div>
      <div class="f-col contact">
        <h4>CONTACT INFO</h4>
        <ul>
          <li><svg viewBox="0 0 10 10"><path d="M5 9.5S1.5 6 1.5 3.8a3.5 3.5 0 0 1 7 0C8.5 6 5 9.5 5 9.5z"/><circle cx="5" cy="3.8" r="1.2"/></svg><span>No-14 B, West Alder Rd,<br>Salem, OR, USA</span></li>
          <li><svg viewBox="0 0 10 10"><path d="M2 1l2 2-1 1.5a6 6 0 0 0 2.5 2.5L7 6l2 2-1.2 1.3C4.5 9 1 5.5.7 2.2z"/></svg><span>1800-555-019</span></li>
          <li><svg viewBox="0 0 10 10"><rect x=".7" y="2" width="8.6" height="6.2"/><path d="M.7 2L5 5.5 9.3 2"/></svg><span>info@quietharborprints.com</span></li>
        </ul>
      </div>
      <div class="f-col quick">
        <h4>QUICK LINKS</h4>
        <ul><li>Artists</li><li>Events</li><li>Shop</li><li>About Us</li></ul>
      </div>
      <div class="f-col">
        <h4>USEFUL LINKS</h4>
        <ul><li>My Account</li><li>Terms of use</li><li>Privacy Policy</li><li>Payment Methods</li></ul>
      </div>
    </div>
    <div class="f-bottom">
      <span>February 19, 2024, Layout_4</span>
      <span>© 2024 <b>QUIET HARBOR PRINTS</b>. All right reserved</span>
      <span class="cards"><i></i><i></i><i></i><i></i></span>
    </div>
  </footer>
</main>

<main class="mobile">
  <header class="m-header">
    <div class="brand">QUIET HARBOR PRINTS</div>
    <svg viewBox="0 0 9 8"><path d="M0 1h9M0 4h9M0 7h9"/></svg>
  </header>

  <section class="m-hero" role="img" aria-label="Gallery interior with framed paintings, wooden floor and a sculpture">
    <div class="kicker">BEGIN AN EXPLORATION THROUGH</div>
    <h1>A GALLERY SHOWCASING ARTIST CREATIVIY</h1>
    <span class="explore">EXPLORE</span>
    <div class="dots"><i></i><i></i><i></i></div>
  </section>

  <section class="m-intro m-pad">
    <h2>THE GALLERY FOR URBAN ART AND CONTEMPORARY ART IN HAMBURG!</h2>
    <p>Lorem ipsum dolor sit amet, consectetur adipiscing elit, sed do eiusmod tempor incididunt ut labore et dolore magna aliqua. Quis ipsum suspendisse ultrices gravida. Risus commodo viverra maecenas accumsan lacus vel facilisis.</p>
    <h3>UPCOMING EVENTS</h3>
    <div class="m-event one" role="img" aria-label="Collage of a woman in profile with sunflowers"><span class="date">MAR. 18,2024</span><span class="ttl">Proin scelerisque dolor vitae<br>augue condimentum</span></div>
    <div class="m-event two" role="img" aria-label="Abstract collage with a large eye"><span class="date">APR. 18,2024</span><span class="ttl">Proin scelerisque dolor vitae<br>augue condimentum</span></div>
    <span class="btn">VIEW ALL EVENTS</span>
  </section>

  <section class="m-art">
    <div class="kicker">NEW ARTWORK</div>
    <h2>UNVEILING OUR<br>EXCLUSIVE ARTWORK</h2>
    <p>Class aptent taciti sociosqu ad litora torquent per conubia nostra, per inceptos himenaeos. Vestibulum non congue ligula, ut sollicitudin arcut taciti sociosqu ad litora torquent per conubia nostra, per inceptos himenaeos.</p>
    <div class="m-card"><span class="ph" role="img" aria-label="Abstract landscape with glowing sun and orange spheres" style="background:linear-gradient(160deg,#2e6d6a 0%,#c8a55a 40%,#d06a2a 70%,#1c3b3c 100%)"></span><div class="cat">CREATIVE</div><div class="nm">MODERN ART</div></div>
    <div class="m-card"><span class="ph" role="img" aria-label="Cubist painting of abstract figures" style="background:linear-gradient(135deg,#8a4a3a,#6a6a8a 45%,#4a3a30)"></span><div class="cat">CREATIVE</div><div class="nm">MODERN ART</div></div>
    <div class="m-card"><span class="ph" role="img" aria-label="White flower on a soft pink background" style="background:linear-gradient(135deg,#f2ddd2,#e9c8bb)"></span><div class="cat">CREATIVE</div><div class="nm">MODERN ART</div></div>
    <span class="viewall">VIEW ALL</span>
  </section>

  <section class="m-popular m-pad">
    <h2>Our Popular Art</h2>
    <p>Etiam ut libero pulvinar, imperdiet enim vel, euismod dui. Nunc nec feugiat ex. Praesent at eros lectus. Duis iaculis posuere arcu quis pretium.</p>
    <div class="frame"><span class="ph" role="img" aria-label="Framed print of mountains inside a silhouette on yellow" style="background:linear-gradient(160deg,#d8b840,#e2e0d8 45%,#222 80%)"></span><div class="nm">CREATIVE ART</div></div>
    <div class="pager"><i></i><i></i><i></i><i></i><i></i></div>
  </section>

  <section class="m-news">
    <div class="kicker">SUBSCRIBE TO</div>
    <h2>OUR NEWSLETTER</h2>
    <small>With our newsletter you won't miss any exhibitions.</small>
    <div class="input"><span>Email Address</span><svg width="8" height="6" viewBox="0 0 12 8"><path d="M0 4h11M8 1l3 3-3 3"/></svg></div>
  </section>

  <section class="m-projects m-pad">
    <h2>OUR LATEST PROJECTS</h2>
    <p>Quisque lacinia elit nulla, non congue dui dignissim at</p>
    <div class="m-proj first" role="img" aria-label="Exhibition hall with framed paintings and track lights" style="background:linear-gradient(180deg,#2a2420,#cfc3b0 45%,#8a6a4a)"><span>Hall of Frame</span></div>
    <div class="m-proj" role="img" aria-label="Gallery corridor lined with vivid paintings" style="background:linear-gradient(90deg,#5a3a2a,#c9b8a0 40%,#8a6a50 70%,#3a2a22)"></div>
    <div class="m-proj" role="img" aria-label="Dim exhibition room with a central display" style="background:linear-gradient(90deg,#3a3430,#7a6a5c 45%,#5a4a40 75%,#2a2420)"></div>
    <span class="btn">VIEW ALL</span>
  </section>

  <footer class="m-footer">
    <div class="block first"><div class="brand">QUIET HARBOR PRINTS</div></div>
    <div class="block contact">
      <h4>CONTACT INFO</h4>
      <ul>
        <li><svg viewBox="0 0 10 10"><path d="M5 9.5S1.5 6 1.5 3.8a3.5 3.5 0 0 1 7 0C8.5 6 5 9.5 5 9.5z"/></svg><span>No-14 B, West Alder Rd,<br>Salem, OR, USA</span></li>
        <li><svg viewBox="0 0 10 10"><path d="M2 1l2 2-1 1.5a6 6 0 0 0 2.5 2.5L7 6l2 2-1.2 1.3C4.5 9 1 5.5.7 2.2z"/></svg><span>1800-555-019</span></li>
        <li><svg viewBox="0 0 10 10"><rect x=".7" y="2" width="8.6" height="6.2"/><path d="M.7 2L5 5.5 9.3 2"/></svg><span>info@quietharborprints.com</span></li>
      </ul>
    </div>
    <div class="block"><h4>QUICK LINKS</h4><ul><li>Artists</li><li>Events</li><li>Shop</li><li>About Us</li></ul></div>
    <div class="block"><h4>USEFUL LINKS</h4><ul><li>My Account</li><li>Terms of use</li><li>Privacy Policy</li><li>Payment Methods</li></ul></div>
    <div class="social"><i></i><i></i><i></i><i></i></div>
    <div class="legal">© 2024 QUIET HARBOR PRINTS. All right reserved<br>February 19, 2024, Layout_4</div>
    <div class="cards"><i></i><i></i><i></i><i></i></div>
  </footer>
</main>

</body>
</html>
```